Business Cards Design for the electrical wholesaler: clean bold dynamic :)

We need a business card design that would follow our latest brand guidelines. As an electrical wholesaler we want to bring a fresh look and feel into the industry. The design should be clean bold and dynamic. It should come alive with the renewed energy of our green colour. Our grey colour should keep things balanced and complement the notion of maturity and responsibility. We employ Lato as a corporate font however are not bound by this font and we’re open to interpretation here.

Target Market(s)

Electrical contractors

Industry/Entity Type

Business

Contact Information for Business Card

Logo
Name & Surname: Halyna Dorosh
Job Title: Director of Marketing
Email: halya.dorosh@quillmail.example
Cell phone: XXX.XXX.XXXX
Address: 20517 - 87 Ave. Edmonton, AB, Canada. T6K 4N8
Business Phone: 780.555.0184
Website: www.brovix.example

Font styles to use
Other font styles liked:
• Lato

Requirements
Must have
• Logo & website
Nice to have
• Brand elements - some of them you may find in the attached Brand Guidelines (e.g. three lines on the background signifying "W")

```html
<!DOCTYPE html>
<html lang="en">
<head>
<meta charset="utf-8">
<title>Brovix business card – Halyna Dorosh</title>
<link rel="stylesheet" href="https://fonts.googleapis.com/css2?family=Lato:wght@400;700;900&display=swap">
<style>
  :root {
    --stage: #9b9b9b;
    --charcoal: #4a4b4d;
    --charcoal-deep: #3f4042;
    --ink: #3d3e40;
    --green: #7ab637;
    --green-soft: #d4e7bf;
    --paper: #ffffff;
    --paper-shade: #ececec;
  }
  * { box-sizing: border-box; margin: 0; padding: 0; }
  html, body { width: 1200px; height: 900px; overflow: hidden; }
  body {
    background: var(--stage);
    font-family: "Lato", Arial, sans-serif;
    display: flex;
    flex-direction: column;
    align-items: center;
    justify-content: center;
    gap: 36px;
  }
  .card {
    position: relative;
    width: 720px;
    height: 411px;
    border-radius: 16px;
    overflow: hidden;
  }

  /* Back side */
  .card-back { background: var(--charcoal); }
  .card-back .brand-echo {
    position: absolute;
    left: 120px; top: 30px;
    width: 520px; height: 350px;
    border-radius: 40px;
    background: radial-gradient(ellipse at center, var(--charcoal-deep) 0%, var(--charcoal) 70%);
  }
  .card-back .brand {
    position: absolute;
    left: 50%; top: 50%;
    transform: translate(-50%, -50%);
    display: flex; align-items: center; gap: 16px;
  }
  .brand-mark { width: 44px; height: 44px; background: var(--green); }
  .brand-name {
    font-weight: 700;
    font-size: 76px;
    line-height: 1;
    letter-spacing: -1px;
  }
  .card-back .brand-name { color: #f2f2f2; }

  /* Front side */
  .card-front {
    background: linear-gradient(160deg, var(--paper) 0%, var(--paper) 55%, var(--paper-shade) 100%);
  }
  .card-front .brand-echo {
    position: absolute;
    left: 400px; top: 118px;
    width: 320px; height: 170px;
    background: linear-gradient(100deg, rgba(212,231,191,0.2) 0%, var(--green-soft) 60%, rgba(212,231,191,0.6) 100%);
  }
  .card-front .brand {
    position: absolute;
    left: 58px; top: 150px;
    display: flex; align-items: center; gap: 14px;
  }
  .card-front .brand-mark { width: 40px; height: 40px; }
  .card-front .brand-name { color: var(--ink); font-size: 68px; }

  .person { position: absolute; left: 440px; top: 44px; }
  .person-name { color: var(--green); font-weight: 900; font-size: 30px; }
  .person-title { color: var(--ink); font-size: 17px; margin-top: 2px; padding-left: 40px; }

  .contact {
    position: absolute;
    left: 64px; top: 262px;
    color: var(--ink);
    font-size: 16px;
    line-height: 1.35;
  }
  .address { margin-bottom: 8px; }
  .contact-line { display: flex; align-items: center; gap: 10px; }
  .contact-line svg { width: 16px; height: 16px; flex: none; }

  .swoosh { position: absolute; inset: 0; }
  .website {
    position: absolute;
    right: 34px; top: 318px;
    color: #f2f2f2;
    font-size: 17px;
    letter-spacing: 2px;
  }
</style>
</head>
<body>

<section class="card card-back" aria-label="Card back">
  <div class="brand-echo" role="img" aria-label="Large faint brand pattern in dark grey"></div>
  <div class="brand">
    <span class="brand-mark"></span>
    <span class="brand-name">brovix</span>
  </div>
</section>

<section class="card card-front" aria-label="Card front">
  <div class="brand-echo" role="img" aria-label="Soft green brand stripes pattern"></div>

  <svg class="swoosh" viewBox="0 0 720 411" aria-hidden="true">
    <path d="M250 411 C400 318 560 282 720 246 L720 254 C560 292 410 330 290 411 Z" fill="var(--green)"/>
    <path d="M310 411 C440 330 580 296 720 272 L720 411 Z" fill="var(--charcoal)"/>
  </svg>

  <div class="brand">
    <span class="brand-mark"></span>
    <span class="brand-name">brovix</span>
  </div>

  <div class="person">
    <div class="person-name">Halyna Dorosh</div>
    <div class="person-title">Director of Marketing</div>
  </div>

  <div class="contact">
    <p class="address">20517 - 87 Ave. Edmonton<br>AB, Canada. T6K 4N8</p>
    <p class="contact-line">
      <svg viewBox="0 0 16 16"><rect x="4" y="1" width="8" height="14" rx="1.5" fill="none" stroke="var(--green)" stroke-width="1.6"/><circle cx="8" cy="12.5" r="0.9" fill="var(--green)"/></svg>
      780.555.0184
    </p>
    <p class="contact-line">
      <svg viewBox="0 0 16 16"><path d="M3 2 L6 2 L7 5.5 L5.3 6.8 C6.2 8.8 7.4 10 9.2 10.8 L10.5 9 L14 10 L14 13 C14 13.6 13.6 14 13 14 C7.5 14 2 8.5 2 3 C2 2.4 2.4 2 3 2 Z" fill="var(--green)"/></svg>
      780.555.0184
    </p>
    <p class="contact-line">
      <svg viewBox="0 0 16 16"><rect x="1" y="3" width="14" height="10" fill="var(--green)"/><path d="M1 3 L8 9 L15 3" fill="none" stroke="#fff" stroke-width="1.2"/></svg>
      halya.dorosh@quillmail.example
    </p>
  </div>

  <p class="website">www.brovix.example</p>
</section>

</body>
</html>
```